Local Flower Farm Needs Business Card Design

I need business cards designed for a flower farm based in Eudora, Kansas.
Business Info:
We are a local cut flower farm located in Eudora, Kansas, founded by Corinne Haldwick. What started as a passion for agriculture and search for more joy in daily life has blossomed into a small business dedicated to providing the community with beautiful, fresh, and sustainable flowers. We specialize in local, seasonal blooms, ensuring that every petal reflects the care and dedication we pour into our craft. Our mission is to deliver the highest quality flowers directly to our customers through local farmers markets and to florists who share our commitment to sustainability. Join us in celebrating the beauty of nature, one bloom at a time!
Contact Details:
Corinne Haldwick
Owner
Phone 913-555-0147
Facebook: Rosalind Thorpe Gardens
Instagram: @RosalindThorpeGardens
Website: RosalindThorpeGardens.example
Target Market(s)
Wholesale to Florists and Direct to Consumer via Farmers Market
Industry/Entity Type
Florist, Farm
Contact Information for Business Card
Name, Contact Info, Logo
Look and feel
Each slider illustrates characteristics of the customer's brand and the style your logo design should communicate.

```html
<!DOCTYPE html>
<html lang="en">
<head>
<meta charset="utf-8">
<title>Rosalind Thorpe Gardens – Business Card</title>
<link href="https://fonts.googleapis.com/css2?family=Arimo:wght@400;700&display=swap" rel="stylesheet">
<style>
  :root {
    --backdrop: #2a2a2a;
    --card-teal: #0d292d;
    --paper: #ffffff;
    --ink-light: #ffffff;
    --ink-dark: #0d292d;
  }
  * { box-sizing: border-box; margin: 0; padding: 0; }
  html, body {
    width: 1200px; height: 900px; overflow: hidden;
    background: var(--backdrop);
    font-family: "Arimo", Arial, sans-serif;
  }
  .canvas { position: relative; width: 1200px; height: 900px; }
  .card {
    position: absolute; left: 250px; width: 700px; height: 400px;
    background: var(--card-teal); border-radius: 28px; overflow: hidden;
  }
  .card--back { top: 30px; }
  .card--front { top: 470px; }

  .brand-seal {
    position: absolute; border-radius: 50%;
    display: flex; align-items: center; justify-content: center; text-align: center;
  }
  .card--back .brand-seal {
    left: 230px; top: 80px; width: 240px; height: 240px;
    border: 1.5px solid var(--ink-light); color: var(--ink-light);
  }
  .brand-name {
    font-family: "Arimo", Arial, sans-serif; font-weight: 400;
    text-transform: uppercase; letter-spacing: 3px; line-height: 1.5;
  }
  .card--back .brand-name { font-size: 19px; }

  .front-disc {
    position: absolute; left: 400px; top: -100px; width: 400px; height: 400px;
    border-radius: 50%; background: var(--paper);
  }
  .card--front .brand-seal {
    left: 445px; top: 25px; width: 230px; height: 230px;
    border: 1.5px solid var(--ink-dark); color: var(--ink-dark);
  }
  .card--front .brand-name { font-size: 19px; }

  .name-marker {
    position: absolute; left: 38px; top: 172px; width: 20px; height: 58px;
    background: var(--paper);
  }
  .person { position: absolute; left: 74px; top: 170px; color: var(--ink-light); }
  .person__name { font-size: 28px; font-weight: 700; letter-spacing: 0.5px; text-transform: uppercase; white-space: nowrap; }
  .person__role { font-size: 18px; font-weight: 400; margin-top: 2px; }

  .contacts {
    position: absolute; left: 190px; top: 290px; list-style: none;
    color: var(--ink-light); font-size: 17px;
  }
  .contacts li { display: flex; align-items: center; gap: 8px; height: 24px; white-space: nowrap; }
  .contacts svg { width: 14px; height: 14px; flex: none; }
</style>
</head>
<body>
<main class="canvas">
  <section class="card card--back" aria-label="Card back">
    <div class="brand-seal">
      <span class="brand-name">Rosalind<br>Thorpe<br>Gardens</span>
    </div>
  </section>

  <section class="card card--front" aria-label="Card front">
    <div class="front-disc"></div>
    <div class="brand-seal">
      <span class="brand-name">Rosalind<br>Thorpe<br>Gardens</span>
    </div>

    <div class="name-marker"></div>
    <div class="person">
      <p class="person__name">Corinne Haldwick</p>
      <p class="person__role">Owner</p>
    </div>

    <ul class="contacts">
      <li>
        <svg viewBox="0 0 16 16" aria-hidden="true"><path fill="#fff" d="M3.6 1.2l2.3 2.6-1.2 1.9c.9 2 2.5 3.6 4.5 4.6l1.9-1.2 2.6 2.3-1.3 2.4C7 13.6 2.4 9 1.3 2.5z"/></svg>
        <span>(913)555-0147</span>
      </li>
      <li>
        <svg viewBox="0 0 16 16" aria-hidden="true"><circle cx="8" cy="8" r="7" fill="#fff"/></svg>
        <span>Rosalind Thorpe Gardens</span>
      </li>
      <li>
        <svg viewBox="0 0 16 16" aria-hidden="true"><circle cx="8" cy="8" r="6.2" fill="none" stroke="#fff" stroke-width="1.6"/></svg>
        <span>@RosalindThorpeGardens</span>
      </li>
      <li>
        <svg viewBox="0 0 16 16" aria-hidden="true"><circle cx="8" cy="8" r="7" fill="#fff"/><path d="M1 8h14M8 1c-3 3-3 11 0 14M8 1c3 3 3 11 0 14" fill="none" stroke="#0d292d" stroke-width="1.2"/></svg>
        <span>RosalindThorpeGardens.example</span>
      </li>
    </ul>
  </section>
</main>
</body>
</html>
```